Business Card Design for Marketing Firm

Looking for business card design for higher end marketing firm. Clean but impressionable/trendy. We are a marketing firm that represents manufacturers in the foodservice equipment and supply industry. Our customers are end users such has hotels, restaurants, country clubs, convention centers and casinos as well as distributors of restaurants supplies and equipment, and manufacturers of foodservice equipment and supplies.
Target Market(s)
Hotels, Restaurants, Supply & Equipment Distributors, Foodservice Manufacturers
Industry/Entity Type
Foodservice/Hospitality
Contact Information for Business Card
Name, Title, Contact Number, Email, Website, Social Media, Address
Requirements
Must have
- Clean & Simple but Serious and Impressionable

```html
<!DOCTYPE html>
<html lang="en">
<head>
<meta charset="utf-8">
<title>Meridian Service Reps — Business Card</title>
<link href="https://fonts.googleapis.com/css2?family=Lato:wght@400;700;900&display=swap" rel="stylesheet">
<style>
  :root {
    --navy: #0b0a82;
    --navy-line: #5a59b8;
    --white: #ffffff;
    --grey-text: #6f6f76;
    --stage: #3a3b3e;
  }
  * { margin: 0; padding: 0; box-sizing: border-box; }
  html, body {
    width: 1200px; height: 952px; overflow: hidden;
    background: var(--stage);
    font-family: "Lato", Arial, sans-serif;
  }
  .sheet {
    position: relative; width: 1200px; height: 952px;
    display: flex; align-items: center; justify-content: center; gap: 60px;
  }
  .card {
    position: relative; width: 510px; height: 292px;
    border-radius: 26px; overflow: hidden;
    box-shadow: 0 14px 30px rgba(0,0,0,.35);
  }

  /* Front */
  .card-front { background: var(--white); }
  .front-brand {
    position: absolute; left: 250px; top: 40px;
    display: flex; align-items: center; gap: 10px;
    color: var(--navy); font-weight: 900; font-size: 30px; letter-spacing: .5px;
  }
  .front-brand .dot { width: 14px; height: 14px; border-radius: 50%; background: var(--navy); }
  .person { position: absolute; left: 40px; top: 112px; }
  .person-name { color: var(--navy); font-size: 19px; letter-spacing: .6px; }
  .person-name strong { font-weight: 900; }
  .person-title { color: var(--grey-text); font-size: 15px; margin-top: 4px; }
  .contact { position: absolute; left: 40px; top: 178px; display: flex; gap: 10px; }
  .icon-bar {
    width: 22px; background: var(--navy); border-radius: 4px;
    display: flex; flex-direction: column; justify-content: space-around; align-items: center;
    padding: 4px 0;
  }
  .icon-bar svg { width: 12px; height: 12px; }
  .contact-lines { color: var(--grey-text); font-size: 13px; line-height: 19px; }
  .address { position: absolute; left: 40px; top: 248px; color: var(--navy); font-size: 13.5px; letter-spacing: .2px; }
  .front-rule { position: absolute; left: 252px; right: 0; top: 240px; height: 1px; background: var(--navy-line); }

  /* Back */
  .card-back { background: var(--navy); }
  .back-rule { position: absolute; left: 0; width: 330px; top: 190px; height: 1.5px; background: var(--white); }
  .back-brand {
    position: absolute; left: 120px; top: 118px;
    color: var(--white); font-weight: 400; font-size: 27px; letter-spacing: 2px;
    display: flex; align-items: center; gap: 12px;
  }
  .back-brand .dot { width: 12px; height: 12px; border-radius: 50%; background: var(--white); }
</style>
</head>
<body>
<main class="sheet">
  <section class="card card-front" aria-label="Card front">
    <div class="front-brand"><span class="dot"></span>Meridian</div>
    <div class="person">
      <p class="person-name">DANIEL R. <strong>WHITFORD</strong></p>
      <p class="person-title">Managing Director</p>
    </div>
    <div class="contact">
      <div class="icon-bar">
        <svg viewBox="0 0 12 12" aria-hidden="true"><path d="M3 1 L5 3.5 L4 5 Q5.5 7.5 7 8 L8.5 7 L11 9 L9.5 11 Q4 10 1 2.5 Z" fill="#fff"/></svg>
        <svg viewBox="0 0 12 12" aria-hidden="true"><rect x="1" y="2.5" width="10" height="7" fill="none" stroke="#fff" stroke-width="1.2"/><path d="M1 2.5 L6 7 L11 2.5" fill="none" stroke="#fff" stroke-width="1.2"/></svg>
        <svg viewBox="0 0 12 12" aria-hidden="true"><path d="M6 11 Q2 6.5 2 4.5 A4 4 0 0 1 10 4.5 Q10 6.5 6 11 Z" fill="#fff"/><circle cx="6" cy="4.5" r="1.4" fill="#0b0a82"/></svg>
      </div>
      <div class="contact-lines">
        <p>+00 987 654 32</p>
        <p>hello@meridianreps.com</p>
        <p>www.meridianreps.com</p>
      </div>
    </div>
    <div class="front-rule"></div>
    <p class="address">1270 Harbor Lane Avenue Portland, OR 97205</p>
  </section>

  <section class="card card-back" aria-label="Card back">
    <div class="back-brand"><span class="dot"></span>MERIDIAN SERVICE REPS</div>
    <div class="back-rule"></div>
  </section>
</main>
</body>
</html>
```